Design a Mobile App for Landscape Businesses

This project is to design the first three screens for a mobile app for Landscape and Lawncare businesses. This app will serve as a directory for homeowners to locate landscape and lawn care businesses and for landscape businesses and contractors to run their business. See the attached PDF for more information and example
Here is the link to the description https://lnkbrev.example/q7z3Kp

Target Market(s)

Landscape and lawn care business, gardeners, home owners

Industry/Entity Type

Landscape Gardening

Logo Text

Verdalink

Colors

Designer to choose colors to be used in the design.

```html
<!DOCTYPE html>
<html lang="en">
<head>
<meta charset="utf-8">
<title>Register Your Business – Verdalink</title>
<link rel="stylesheet" href="https://fonts.googleapis.com/css2?family=Nunito+Sans:wght@300;400;600;700;800&display=swap">
<style>
  :root {
    --ink: #1d2b3a;
    --ink-soft: #2c3a48;
    --green: #3aa83a;
    --track: #dfe3e7;
    --page: #eff3f6;
    --surface: #ffffff;
    --field-border: #dde2e7;
  }
  * { box-sizing: border-box; margin: 0; padding: 0; }
  html, body { width: 675px; height: 1200px; overflow: hidden; }
  body {
    position: relative;
    background: var(--page);
    font-family: "Nunito Sans", Arial, sans-serif;
    color: var(--ink);
  }
  .status-bar {
    position: absolute; left: 0; top: 0; width: 675px; height: 36px;
    background: var(--surface);
    display: flex; align-items: center; justify-content: flex-end;
    gap: 8px; padding-right: 18px;
    font-size: 20px; color: #222;
  }
  .status-bar svg { display: block; }
  .app-header {
    position: absolute; left: 0; top: 36px; width: 675px; height: 92px;
    background: var(--surface);
  }
  .app-header__title {
    position: absolute; left: 18px; top: 24px;
    font-size: 27px; font-weight: 800; letter-spacing: 0.1px;
  }
  .app-header__close { position: absolute; right: 20px; top: 24px; }
  .progress {
    position: absolute; left: 0; top: 128px; width: 675px; height: 9px;
    background: var(--track);
  }
  .progress__fill { width: 346px; height: 100%; background: var(--green); }
  .step-title {
    position: absolute; left: 18px; top: 186px;
    font-size: 38px; font-weight: 300; color: var(--ink-soft);
  }
  .field-label {
    position: absolute;
    font-size: 19px; font-weight: 800; text-transform: uppercase;
    letter-spacing: 0.3px;
  }
  .field {
    position: absolute; height: 80px;
    background: var(--surface);
    border: 1.5px solid var(--field-border);
    border-radius: 3px;
    display: flex; align-items: center; padding-left: 20px;
    font-size: 23px; color: var(--ink);
  }
  .field--select { font-weight: 800; justify-content: space-between; padding-right: 22px; }
  .next-button {
    position: absolute; left: 20px; top: 1096px; width: 637px; height: 83px;
    background: var(--green); border-radius: 6px;
    display: flex; align-items: center; justify-content: center; gap: 14px;
    color: #fff; font-size: 23px; font-weight: 800;
  }
</style>
</head>
<body>
  <div class="status-bar">
    <svg width="20" height="20" viewBox="0 0 20 20" aria-hidden="true"><circle cx="10" cy="11" r="7" fill="none" stroke="#222" stroke-width="2"/><path d="M10 7v4l3 2" stroke="#222" stroke-width="2" fill="none"/></svg>
    <svg width="22" height="18" viewBox="0 0 22 18" aria-hidden="true"><path d="M11 17L0 4a16 16 0 0 1 22 0z" fill="#222"/></svg>
    <svg width="18" height="18" viewBox="0 0 18 18" aria-hidden="true"><path d="M18 0v18H0z" fill="#222"/></svg>
    <svg width="11" height="20" viewBox="0 0 11 20" aria-hidden="true"><rect x="1" y="3" width="9" height="16" fill="none" stroke="#222" stroke-width="2"/><rect x="3.5" y="0.5" width="4" height="3" fill="#222"/></svg>
    <span>16:54</span>
  </div>

  <header class="app-header">
    <h1 class="app-header__title">Register Your Business</h1>
    <svg class="app-header__close" width="34" height="34" viewBox="0 0 34 34" aria-label="Close">
      <path d="M3 3l28 28M31 3L3 31" stroke="var(--ink)" stroke-width="3.4" stroke-linecap="round"/>
    </svg>
  </header>

  <div class="progress"><div class="progress__fill"></div></div>

  <h2 class="step-title">About You (1/2)</h2>

  <label class="field-label" style="left:18px; top:278px;">Business Name</label>
  <div class="field" style="left:18px; top:319px; width:639px;">Verdalink Inc.</div>

  <label class="field-label" style="left:18px; top:420px;">Address</label>
  <div class="field" style="left:18px; top:459px; width:639px;">418 Larkmoor Lane</div>

  <label class="field-label" style="left:18px; top:558px;">City</label>
  <div class="field" style="left:18px; top:598px; width:639px;">New York</div>

  <label class="field-label" style="left:18px; top:702px;">State</label>
  <div class="field field--select" style="left:18px; top:740px; width:310px; height:83px;">
    <span>New York</span>
    <svg width="20" height="12" viewBox="0 0 20 12" aria-hidden="true"><path d="M2 2l8 8 8-8" stroke="var(--ink)" stroke-width="2.4" fill="none" stroke-linecap="round" stroke-linejoin="round"/></svg>
  </div>

  <label class="field-label" style="left:347px; top:702px;">Zip Code</label>
  <div class="field" style="left:347px; top:740px; width:310px; height:83px;">10482</div>

  <div class="next-button">
    <span>Next</span>
    <svg width="28" height="24" viewBox="0 0 28 24" aria-hidden="true"><path d="M2 12h22M15 3l9 9-9 9" stroke="#fff" stroke-width="2.8" fill="none" stroke-linecap="round" stroke-linejoin="round"/></svg>
  </div>
</body>
</html>
```